Local Flower Farm Needs Business Card Design

I need business cards designed for a flower farm based in Eudora, Kansas.
Business Info:
We are a local cut flower farm located in Eudora, Kansas, founded by Corinne Haldwick. What started as a passion for agriculture and search for more joy in daily life has blossomed into a small business dedicated to providing the community with beautiful, fresh, and sustainable flowers. We specialize in local, seasonal blooms, ensuring that every petal reflects the care and dedication we pour into our craft. Our mission is to deliver the highest quality flowers directly to our customers through local farmers markets and to florists who share our commitment to sustainability. Join us in celebrating the beauty of nature, one bloom at a time!
Contact Details:
Corinne Haldwick
Owner
Phone 913-555-0147
Facebook: Rosalind Thorpe Gardens
Instagram: @RosalindThorpeGardens
Website: RosalindThorpeGardens.example
Target Market(s)
Wholesale to Florists and Direct to Consumer via Farmers Market
Industry/Entity Type
Florist, Farm
Contact Information for Business Card
Name, Contact Info, Logo
Look and feel
Each slider illustrates characteristics of the customer's brand and the style your logo design should communicate.

```html
<!DOCTYPE html>
<html lang="en">
<head>
<meta charset="utf-8">
<title>Rosalind Thorpe Gardens – Business Card</title>
<link href="https://fonts.googleapis.com/css2?family=Source+Serif+4:opsz,wght@8..60,400;8..60,700&family=Tinos:wght@400;700&display=swap" rel="stylesheet">
<style>
  :root {
    --ink: #0b272d;
    --paper: #ffffff;
    --backdrop: #2e2e2e;
    --rule: #1d2b2e;
  }
  * { box-sizing: border-box; margin: 0; padding: 0; }
  html, body { width: 1200px; height: 689px; overflow: hidden; }
  body {
    background: var(--backdrop);
    display: flex;
    align-items: center;
    justify-content: center;
    gap: 60px;
    font-family: "Tinos", "Times New Roman", serif;
  }
  .card {
    width: 520px;
    height: 298px;
    border-radius: 22px;
    position: relative;
    overflow: hidden;
  }
  .card--front { background: var(--ink); color: var(--paper); }
  .card--back { background: var(--paper); color: var(--ink); }

  .brand-seal {
    position: absolute;
    border-radius: 50%;
    display: flex;
    align-items: center;
    justify-content: center;
    text-align: center;
    font-family: "Tinos", "Times New Roman", serif;
    font-weight: 400;
    letter-spacing: 0.14em;
    text-transform: uppercase;
    line-height: 1.5;
  }
  .card--front .brand-seal {
    width: 210px; height: 210px;
    left: 155px; top: 44px;
    border: 1.5px solid var(--paper);
    font-size: 17px;
  }
  .card--back .brand-seal {
    width: 180px; height: 180px;
    left: 44px; top: 62px;
    border: 1.5px solid var(--ink);
    font-size: 14px;
  }

  .divider {
    position: absolute;
    left: 262px; top: 52px;
    width: 1px; height: 196px;
    background: var(--rule);
  }
  .contact {
    position: absolute;
    left: 290px; top: 70px;
  }
  .contact__name {
    font-family: "Source Serif 4", "Times New Roman", serif;
    font-weight: 700;
    font-size: 25px;
    line-height: 1.1;
  }
  .contact__role {
    font-size: 14px;
    margin: 4px 0 20px 6px;
  }
  .contact__list {
    list-style: none;
    font-size: 12.5px;
    line-height: 1.55;
    margin-left: 6px;
  }
  .contact__list b { font-weight: 700; }
</style>
</head>
<body>
  <section class="card card--front" aria-label="Card front">
    <div class="brand-seal">Rosalind<br>Thorpe<br>Gardens</div>
  </section>

  <section class="card card--back" aria-label="Card back">
    <div class="brand-seal">Rosalind<br>Thorpe<br>Gardens</div>
    <div class="divider"></div>
    <div class="contact">
      <h1 class="contact__name">Corinne Haldwick</h1>
      <p class="contact__role">Owner</p>
      <ul class="contact__list">
        <li><b>Facebook:</b> Rosalind Thorpe Gardens</li>
        <li><b>Instagram:</b> @RosalindThorpeGardens</li>
        <li><b>Website:</b> RosalindThorpeGardens.example</li>
      </ul>
    </div>
  </section>
</body>
</html>
```